Custom hot rod builder needs a website for launch of new business where he will build luxury garages

We need a website that gives a WOW first impression for "Summit Carports". This is a new business so photos are renderings but we need it to really attract a particular audience. Our initial business is custom hot rods so now we are building garages for them. These will be like luxury "homes" for cars! I will attach our new logo. Website needs to feel powerful and prestigious.

Target Market(s)

middle aged men, car enthusiasts

Industry/Entity Type

automotive, construction

Coding

Coded - Design and coding required

Number of Pages Required

2 page

Font styles to use
Serif

Colors
0054AA
0677BA
7BADD7
CADEEF
E8F1F8

Requirements
Must have
• a WOW factor. luxury. contact form.
Nice to have
• ?

```html
<!DOCTYPE html>
<html lang="en">
<head>
<meta charset="utf-8">
<title>Summit Carports — Custom Hot Rod Luxury Garages</title>
<link rel="stylesheet" href="https://fonts.googleapis.com/css2?family=Syncopate:wght@400;700&family=Nunito:wght@400;600;700&family=Oswald:wght@500;600&display=swap">
<style>
:root{
  --blue-deep:#0054AA;
  --blue-mid:#0677BA;
  --blue-bright:#2AA6E3;
  --blue-soft:#7BADD7;
  --blue-pale:#CADEEF;
  --blue-mist:#E8F1F8;
  --ink:#333;
  --ink-soft:#555;
  --white:#fff;
  --night:#050608;
  --star:#F2A516;
}
*{box-sizing:border-box;margin:0;padding:0}
html,body{width:1200px;height:3995px;overflow:hidden}
body{position:relative;background:var(--white);font-family:'Nunito',sans-serif;color:var(--ink)}
.abs{position:absolute}
.display{font-family:'Syncopate',sans-serif;text-transform:none;letter-spacing:3px;font-weight:700;line-height:1.1}
.display .light{color:var(--blue-bright)}
.display .dark{color:var(--blue-deep)}
.brand{font-family:'Nunito',sans-serif;font-weight:700;color:var(--blue-bright);display:flex;align-items:center;gap:10px}
.brand .mark{width:30px;height:30px;border-radius:50%;background:var(--blue-bright)}
.btn{display:inline-block;background:var(--blue-bright);color:var(--white);font-size:16px;padding:10px 18px;border-radius:2px;text-align:center}
.underline-wave{display:block;margin:10px auto 0;width:60px;height:8px}

/* header */
.site-header{left:0;top:0;width:1200px;height:90px;background:var(--white);box-shadow:0 2px 6px rgba(0,0,0,.15);z-index:3}
.site-header .brand{position:absolute;left:194px;top:26px;font-size:26px}
.nav{position:absolute;left:575px;top:33px;display:flex;gap:28px;font-size:14px;color:#222}
.nav .active{color:var(--blue-mid);border-bottom:1px solid var(--blue-mid)}
.header-phone{position:absolute;left:840px;top:16px;height:58px;padding-left:14px;border-left:1px solid #ddd;display:flex;align-items:center;gap:8px;color:var(--blue-mid);font-size:21px}

/* hero */
.hero{left:0;top:90px;width:1200px;height:553px;overflow:hidden}
.hero-photo{position:absolute;inset:0;background:linear-gradient(180deg,#3a2616 0%,#6b4526 35%,#4a3a33 60%,#2b3a44 100%)}
.hero-title{position:absolute;left:0;width:100%;top:118px;text-align:center;font-family:'Oswald',sans-serif;font-weight:500;font-size:38px;color:var(--white);text-shadow:0 2px 6px rgba(0,0,0,.6)}
.hero .btn{position:absolute;left:526px;top:181px;font-size:16px}
.hero-arrow{position:absolute;top:258px;width:34px;height:34px}
.hero-wave{position:absolute;left:0;bottom:0;width:1200px;height:120px}

/* welcome */
.welcome-photo{left:188px;top:724px;width:330px;height:296px;background:linear-gradient(180deg,#b8c3cc 0%,#e8e9e6 45%,#6d7b6a 75%,#9aa0a4 100%)}
.years-badge{left:344px;top:888px;width:183px;height:152px;background:#5d6469;border:4px solid var(--white);color:var(--white);text-align:center;font-family:'Oswald',sans-serif}
.years-badge .num{font-size:88px;font-weight:500;line-height:1;margin-top:8px}
.years-badge .num sup{font-size:26px;vertical-align:-6px}
.years-badge .label{font-size:19px;font-weight:400}
.welcome-text{left:567px;top:712px;width:445px}
.welcome-text h2{font-size:26px}
.welcome-text .underline-wave{margin:20px 0 16px}
.welcome-text p{font-size:11.5px;line-height:23px;color:var(--ink-soft);margin-bottom:8px}
.welcome-text .btn{margin-top:10px}

/* section headings */
.section-title{left:0;width:1200px;text-align:center;font-size:27px}

/* offers */
.offer{width:403px;height:113px;background:var(--white);border:1px solid #eee;box-shadow:0 2px 8px rgba(0,0,0,.08);display:flex;align-items:center;padding:0 14px 0 22px;gap:20px}
.offer .icon{flex:none;width:50px;height:50px;border-radius:50%;background:var(--white);box-shadow:2px 3px 8px rgba(0,0,0,.15);display:flex;align-items:center;justify-content:center}
.offer h3{font-size:14px;font-weight:700;color:var(--blue-deep);margin-bottom:4px}
.offer p{font-size:11px;line-height:20px;color:var(--ink-soft)}

/* call to action bands */
.cta{left:192px;width:812px;height:250px;background:var(--blue-deep);border-radius:10px;text-align:center;color:var(--white);z-index:1}
.cta-shadow{left:222px;width:754px;height:40px;background:var(--blue-pale);border-radius:0 0 10px 10px}
.cta h2{font-family:'Syncopate',sans-serif;font-weight:700;font-size:30px;letter-spacing:5px;line-height:40px;margin-top:62px}
.cta .btn{margin-top:10px}

/* gallery */
.project{width:262px;height:260px;background:var(--white);border:1px solid #e5e5e5;box-shadow:0 2px 6px rgba(0,0,0,.08)}
.project .shot{height:222px}
.project .caption{height:37px;display:flex;align-items:center;justify-content:center;font-size:12px;color:#333}
.project.active .caption{background:var(--blue-deep);color:var(--white)}

/* reviews */
.review{width:396px;height:199px;background:var(--white);box-shadow:0 2px 10px rgba(0,0,0,.08);padding:22px 28px}
.review p{font-size:11px;line-height:20px;color:#777}
.review .name{margin-top:20px;font-size:12px;color:var(--blue-mid)}
.review .stars{color:var(--star);font-size:13px;letter-spacing:1px}
.review .quote{position:absolute;right:26px;bottom:20px;font-family:Georgia,serif;font-size:110px;line-height:.6;color:var(--blue-pale);height:50px}
.dots{left:520px;top:2955px;display:flex;gap:10px}
.dots span{width:24px;height:3px;background:#ddd}
.dots span.on{background:var(--blue-deep)}

/* footer */
.footer-wave{left:0;top:3390px;width:1200px;height:110px}
.site-footer{left:0;top:3495px;width:1200px;height:450px;background:var(--night);color:var(--white)}
.site-footer .brand{position:absolute;left:188px;top:-10px;font-size:34px}
.footer-heading{position:absolute;font-size:15px;letter-spacing:3px}
.contact-item{position:absolute;left:188px;display:flex;gap:12px;font-size:13px;line-height:20px}
.contact-item a{color:var(--blue-bright)}
.form-intro{position:absolute;left:505px;top:96px;width:520px;font-size:11px;line-height:18px}
.field{position:absolute;border-bottom:1px solid #444;height:34px;display:flex;align-items:center;gap:10px;font-size:11.5px}
.site-footer .btn{position:absolute;left:504px;top:330px;width:148px;padding:12px 0;font-size:16px}
.copyright{left:0;top:3945px;width:1200px;height:50px;background:var(--blue-bright);color:var(--white);font-size:12px;display:flex;align-items:center;justify-content:center}
</style>
</head>
<body>

<header class="site-header abs">
  <div class="brand"><span class="mark"></span>Summit Carports</div>
  <nav class="nav"><span class="active">Home</span><span>Work Gallery</span><span>Contact Us</span></nav>
  <div class="header-phone">
    <svg width="22" height="22" viewBox="0 0 24 24" fill="none" stroke="currentColor" stroke-width="1.6"><path d="M5 3h4l2 5-3 2a12 12 0 0 0 6 6l2-3 5 2v4a2 2 0 0 1-2 2A18 18 0 0 1 3 5a2 2 0 0 1 2-2z"/></svg>
    555.014.2288
  </div>
</header>

<section class="hero abs">
  <div class="hero-photo" role="img" aria-label="Rendering of a luxury garage interior with brick walls, wood ceiling and classic hot rods on display"></div>
  <h1 class="hero-title">We Build Custom Hot Rod Luxury Garages</h1>
  <span class="btn">Contact Us Today</span>
  <svg class="hero-arrow" style="left:90px" viewBox="0 0 34 34" fill="none" stroke="#fff" stroke-width="1.5"><circle cx="17" cy="17" r="15"/><path d="M19 11l-6 6 6 6"/></svg>
  <svg class="hero-arrow" style="left:1078px" viewBox="0 0 34 34" fill="none" stroke="#fff" stroke-width="1.5"><circle cx="17" cy="17" r="15"/><path d="M15 11l6 6-6 6"/></svg>
  <svg class="hero-wave" viewBox="0 0 1200 120" preserveAspectRatio="none">
    <path d="M0 70 C250 10 520 20 760 80 C930 120 1080 110 1200 70 L1200 120 L0 120Z" fill="#fff"/>
    <path d="M0 78 C220 20 500 40 760 95 C930 125 1080 118 1200 96" fill="none" stroke="var(--blue-bright)" stroke-width="7"/>
    <path d="M0 70 C250 10 520 20 760 80" fill="none" stroke="var(--blue-deep)" stroke-width="3"/>
  </svg>
</section>

<div class="welcome-photo abs" role="img" aria-label="Rendering of a modern garage building with palm trees"></div>
<div class="years-badge abs"><div class="num">20<sup>+</sup></div><div class="label">Years Experience</div></div>
<div class="welcome-text abs">
  <h2 class="display"><span class="light">Welcome To</span><br><span class="dark">Summit Carports</span></h2>
  <svg class="underline-wave" viewBox="0 0 60 8"><path d="M2 6 Q30 -2 58 6" fill="none" stroke="var(--blue-deep)" stroke-width="3"/></svg>
  <p>Lorem ipsum dolor sit amet, consectetuer adipiscing elit, sed dim nonummy nibh euismod tincidunt ut laoreet dolore magna aliquam erat volutpat. Ut wisi enim ad minim veniam, quis nostrud exerci.</p>
  <p>Lorem ipsum dolor sit amet, consectetuer adipiscing elit, sed dim nonummy nibh euismod tincidunt ut laoreet dolore magna aliquam erat volutpat. Ut wisi enim ad minim veniam, quis nostrud exerci tation ullamcorper suscipit lobortis nisl ut aliquip ex ea commodo consequat. Duis aute</p>
  <span class="btn">Contact Us</span>
</div>

<h2 class="section-title display abs" style="top:1136px"><span class="light">What We</span> <span class="dark">Offer</span>
  <svg class="underline-wave" viewBox="0 0 60 8"><path d="M2 6 Q30 -2 58 6" fill="none" stroke="var(--blue-deep)" stroke-width="3"/></svg></h2>

<div class="offer abs" style="left:186px;top:1209px">
  <div class="icon"><svg width="26" height="26" viewBox="0 0 24 24" fill="none" stroke="var(--blue-mid)" stroke-width="1.5"><path d="M4 12l5 5 11-11"/></svg></div>
  <div><h3>Loyalty Programs</h3><p>Lorem ipsum dolor sit amet, consectetuer adipiscing elit, sed dim nonummy nibh euismod.</p></div>
</div>
<div class="offer abs" style="left:608px;top:1209px">
  <div class="icon"><svg width="26" height="26" viewBox="0 0 24 24" fill="none" stroke="var(--blue-mid)" stroke-width="1.5"><circle cx="12" cy="10" r="7"/><path d="M12 6l1.2 2.6 2.8.3-2.1 1.9.6 2.8L12 12.2 9.5 13.6l.6-2.8L8 8.9l2.8-.3z"/><path d="M8 16l-2 6 4-2 2 2 2-2 4 2-2-6"/></svg></div>
  <div><h3>20 Years Experience</h3><p>Lorem ipsum dolor sit amet, consectetuer adipiscing elit, sed dim nonummy nibh euismod.</p></div>
</div>
<div class="offer abs" style="left:186px;top:1344px">
  <div class="icon"><svg width="26" height="26" viewBox="0 0 24 24" fill="none" stroke="var(--blue-mid)" stroke-width="1.5"><path d="M3 12l9-9h8v8l-9 9z"/><circle cx="16" cy="8" r="1.5"/></svg></div>
  <div><h3>Always The Best Value</h3><p>Lorem ipsum dolor sit amet, consectetuer adipiscing elit, sed dim nonummy nibh euismod.</p></div>
</div>
<div class="offer abs" style="left:608px;top:1344px">
  <div class="icon"><svg width="26" height="26" viewBox="0 0 24 24" fill="none" stroke="var(--blue-mid)" stroke-width="1.5"><path d="M4 14v-2a8 8 0 0 1 16 0v2"/><rect x="3" y="13" width="4" height="6" rx="1"/><rect x="17" y="13" width="4" height="6" rx="1"/><path d="M19 19v1a2 2 0 0 1-2 2h-4"/></svg></div>
  <div><h3>24 Hour Customer Service Available</h3><p>Lorem ipsum dolor sit amet, consectetuer adipiscing elit, sed dim nonummy nibh euismod.</p></div>
</div>

<div class="cta abs" style="top:1530px">
  <h2>To Build Your<br>Luxury “homes” For Cars!</h2>
  <span class="btn">Contact Us Today</span>
</div>
<div class="cta-shadow abs" style="top:1758px"></div>

<h2 class="section-title display abs" style="top:1877px"><span class="light">Work</span> <span class="dark">Gallery</span>
  <svg class="underline-wave" viewBox="0 0 60 8"><path d="M2 6 Q30 -2 58 6" fill="none" stroke="var(--blue-deep)" stroke-width="3"/></svg></h2>

<div class="project active abs" style="left:186px;top:1944px"><div class="shot" role="img" aria-label="Garage with classic hot rods parked inside" style="background:linear-gradient(180deg,#7a6a4a,#3f4a52 60%,#b9c2c9)"></div><div class="caption">Project 1 @ Harbor Ridge, Oakvale</div></div>
<div class="project abs" style="left:468px;top:1944px"><div class="shot" role="img" aria-label="Wood-ceiling showroom with parked classic cars" style="background:linear-gradient(180deg,#8a5a32,#4d3a2e 55%,#4e6872)"></div><div class="caption">Project 2 @ Harbor Ridge, Oakvale</div></div>
<div class="project abs" style="left:752px;top:1944px"><div class="shot" role="img" aria-label="Workshop garage with hot rods" style="background:linear-gradient(180deg,#4a4038,#2f2c2a 55%,#6d665e)"></div><div class="caption">Project 3 @ Harbor Ridge, Oakvale</div></div>
<div class="project abs" style="left:186px;top:2235px"><div class="shot" role="img" aria-label="Vintage car collection in a bright garage" style="background:linear-gradient(180deg,#b59a72,#5c5a6a 55%,#d8d4cc)"></div><div class="caption">Project 4 @ Harbor Ridge, Oakvale</div></div>
<div class="project abs" style="left:468px;top:2235px"><div class="shot" role="img" aria-label="Dark garage with polished hot rods" style="background:linear-gradient(180deg,#222,#4a4428 55%,#1a1a1a)"></div><div class="caption">Project 5 @ Harbor Ridge, Oakvale</div></div>
<div class="project abs" style="left:752px;top:2235px"><div class="shot" role="img" aria-label="Large garage hall with custom cars" style="background:linear-gradient(180deg,#5a5e62,#3c3734 55%,#77706a)"></div><div class="caption">Project 6 @ Harbor Ridge, Oakvale</div></div>

<span class="btn abs" style="left:527px;top:2533px;width:126px;padding:11px 0">View All</span>

<h2 class="section-title display abs" style="top:2655px"><span class="light">Happy Customer</span> <span class="dark">Reviews</span>
  <svg class="underline-wave" viewBox="0 0 60 8"><path d="M2 6 Q30 -2 58 6" fill="none" stroke="var(--blue-deep)" stroke-width="3"/></svg></h2>

<div class="review abs" style="left:189px;top:2723px">
  <p>Lorem ipsum dolor sit amet, consectetuer adipiscing elit, sed dim nonummy nibh euismod tincidunt ut laoreet dore magna aliquam erat volutpat. Ut wisi enim ad minim veniam, quis nostrud exerci tation ullamcorper suscipit lobortis nisl ut aliquip ex ea commodo consequat. Duis aute</p>
  <div class="name">Marla T.</div><div class="stars">★★★★★</div>
  <div class="quote">”</div>
</div>
<div class="review abs" style="left:614px;top:2723px">
  <p>Lorem ipsum dolor sit amet, consectetuer adipiscing elit, sed dim nonummy nibh euismod tincidunt ut laoreet dore magna aliquam erat volutpat. Ut wisi enim ad minim veniam, quis nostrud exerci tation ullamcorper suscipit lobortis nisl ut aliquip ex ea commodo consequat. Duis aute</p>
  <div class="name">Denise R.</div><div class="stars">★★★★★</div>
  <div class="quote">”</div>
</div>
<div class="dots abs"><span></span><span></span><span class="on"></span><span></span><span></span></div>

<div class="cta abs" style="top:3032px">
  <h2>To Build Your<br>Luxury custom hot rods Garages!</h2>
  <span class="btn">Contact Us Today</span>
</div>
<div class="cta-shadow abs" style="top:3262px"></div>

<svg class="footer-wave abs" viewBox="0 0 1200 110" preserveAspectRatio="none">
  <path d="M0 90 C200 40 380 10 560 30 C760 55 950 110 1200 60 L1200 110 L0 110Z" fill="var(--night)"/>
  <path d="M560 28 C760 52 950 104 1200 56" fill="none" stroke="var(--blue-bright)" stroke-width="8"/>
</svg>

<footer class="site-footer abs">
  <div class="brand"><span class="mark"></span>Summit Carports</div>

  <h3 class="footer-heading display" style="left:190px;top:56px"><span class="light">Contact</span> <span style="color:#fff">Details</span></h3>
  <svg class="abs" style="left:190px;top:80px" width="60" height="8" viewBox="0 0 60 8"><path d="M2 6 Q30 -2 58 6" fill="none" stroke="#fff" stroke-width="2"/></svg>

  <div class="contact-item" style="top:110px"><svg width="20" height="22" viewBox="0 0 24 24" fill="none" stroke="var(--blue-bright)" stroke-width="1.5"><path d="M12 22s-7-7-7-12a7 7 0 0 1 14 0c0 5-7 12-7 12z"/><circle cx="12" cy="10" r="2.5"/></svg><div>Summit Carports<br>Street Name, City Name<br>State Zipcode</div></div>
  <div class="contact-item" style="top:192px"><svg width="20" height="22" viewBox="0 0 24 24" fill="none" stroke="var(--blue-bright)" stroke-width="1.5"><path d="M5 3h4l2 5-3 2a12 12 0 0 0 6 6l2-3 5 2v4a2 2 0 0 1-2 2A18 18 0 0 1 3 5a2 2 0 0 1 2-2z"/></svg><div>Call Us<br>555.014.2288</div></div>
  <div class="contact-item" style="top:256px"><svg width="20" height="22" viewBox="0 0 24 24" fill="none" stroke="var(--blue-bright)" stroke-width="1.5"><rect x="3" y="6" width="18" height="13" rx="1"/><path d="M3 7l9 7 9-7"/></svg><div>Email Us<br>inquiry@summitcarports.com</div></div>
  <div class="contact-item" style="top:320px"><svg width="20" height="22" viewBox="0 0 24 24" fill="none" stroke="var(--blue-bright)" stroke-width="1.5"><path d="M12 22s-7-7-7-12a7 7 0 0 1 14 0c0 5-7 12-7 12z"/><circle cx="12" cy="10" r="2.5"/></svg><div>Location Map<br><a>View Directions</a></div></div>

  <h3 class="footer-heading display" style="left:508px;top:56px"><span class="light">Get</span> <span style="color:#fff">In Touch</span></h3>
  <svg class="abs" style="left:508px;top:80px" width="60" height="8" viewBox="0 0 60 8"><path d="M2 6 Q30 -2 58 6" fill="none" stroke="#fff" stroke-width="2"/></svg>
  <p class="form-intro">If you would like to know more about our services please call or provide the information below.<br>Thank you for your interest in Summit Carports</p>

  <div class="field" style="left:505px;top:140px;width:240px"><svg width="14" height="14" viewBox="0 0 24 24" fill="none" stroke="var(--blue-bright)" stroke-width="2"><circle cx="12" cy="8" r="4"/><path d="M4 21c0-4 4-6 8-6s8 2 8 6"/></svg>First Name</div>
  <div class="field" style="left:773px;top:140px;width:240px"><svg width="14" height="14" viewBox="0 0 24 24" fill="none" stroke="var(--blue-bright)" stroke-width="2"><circle cx="12" cy="8" r="4"/><path d="M4 21c0-4 4-6 8-6s8 2 8 6"/></svg>Last Name</div>
  <div class="field" style="left:505px;top:193px;width:240px"><svg width="14" height="14" viewBox="0 0 24 24" fill="none" stroke="var(--blue-bright)" stroke-width="2"><rect x="3" y="6" width="18" height="13"/><path d="M3 7l9 7 9-7"/></svg>Email</div>
  <div class="field" style="left:773px;top:187px;width:240px"><svg width="14" height="14" viewBox="0 0 24 24" fill="none" stroke="var(--blue-bright)" stroke-width="2"><path d="M5 3h4l2 5-3 2a12 12 0 0 0 6 6l2-3 5 2v4a2 2 0 0 1-2 2A18 18 0 0 1 3 5a2 2 0 0 1 2-2z"/></svg>Phone</div>
  <div class="field" style="left:505px;top:244px;width:508px;height:62px;align-items:flex-start"><svg width="14" height="14" viewBox="0 0 24 24" fill="none" stroke="var(--blue-bright)" stroke-width="2"><path d="M4 5h16v11H9l-5 4z"/></svg>Message</div>
  <span class="btn">Submit Now</span>
</footer>

<div class="copyright abs">© 2022 Summit Carports, All Rights Reserved.</div>

</body>
</html>
```